business card

Business card for new business.
Red and black corporate colors.
Card can have an Indsutrial feel to it. Feel free to add Rust, Bolted steel, or graphics as you see fit. We provide highly specialized services to the below mentioned industries.
Keep information out of corners so that if I want I can choose rounded corners.
Information
- front. name - title - phone - email
- Rear
Refining - Rail - Infrastructure - Mining - Energy
Calgary - Edmonton - Fort McMurray - Revelstoke - Vancouver

```html
<!DOCTYPE html>
<html lang="en">
<head>
<meta charset="utf-8">
<title>Ironvale Business Card</title>
<link rel="stylesheet" href="https://fonts.googleapis.com/css2?family=Roboto:wght@400;500;700&display=swap">
<style>
  :root {
    --backdrop: #5a4838;
    --card-white: #f3f3f3;
    --card-black: #222222;
    --brand-red: #e3061b;
    --text-grey: #555555;
    --title-grey: #8a8a8a;
    --logo-grey: #7c7c7c;
  }
  html, body {
    margin: 0;
    padding: 0;
    width: 1200px;
    height: 960px;
    overflow: hidden;
    background: var(--backdrop);
    font-family: "Roboto", Arial, sans-serif;
  }
  .stage {
    position: relative;
    width: 1200px;
    height: 960px;
  }
  .card {
    position: absolute;
    box-sizing: border-box;
  }
  .card-front {
    left: 313px;
    top: 113px;
    width: 600px;
    height: 342px;
    background: var(--card-white);
    border: 5px solid var(--brand-red);
    text-align: center;
    color: var(--text-grey);
  }
  .person-name {
    position: absolute;
    left: 0; right: 0;
    top: 86px;
    margin: 0;
    font-size: 23px;
    font-weight: 700;
    color: var(--brand-red);
    line-height: 1;
  }
  .person-title {
    position: absolute;
    left: 0; right: 0;
    top: 111px;
    margin: 0;
    font-size: 15px;
    font-weight: 500;
    color: var(--title-grey);
    line-height: 1;
  }
  .contact {
    position: absolute;
    left: 0; right: 0;
    top: 137px;
    margin: 0;
    font-size: 14.5px;
    line-height: 19px;
    color: var(--text-grey);
  }
  .divider-arrow {
    position: absolute;
    left: 50%;
    top: 182px;
    width: 10px;
    height: 20px;
    margin-left: -5px;
  }
  .services {
    position: absolute;
    left: 0; right: 0;
    top: 207px;
    margin: 0;
    font-size: 14.5px;
    line-height: 18px;
    color: var(--text-grey);
  }
  .dot {
    color: var(--brand-red);
    font-size: 12px;
  }
  .card-back {
    left: 311px;
    top: 471px;
    width: 602px;
    height: 344px;
    background: var(--card-black);
  }
  .brand-name {
    position: absolute;
    left: 0; right: 0;
    top: 136px;
    margin: 0;
    text-align: center;
    font-size: 72px;
    font-weight: 700;
    letter-spacing: 1px;
    line-height: 1;
    color: var(--logo-grey);
  }
</style>
</head>
<body>
  <main class="stage">
    <section class="card card-front" aria-label="Card front">
      <h1 class="person-name">MARCUS HALE</h1>
      <p class="person-title">CEO/FOUNDER</p>
      <p class="contact">555 014 7720<br>info@ironvale.com | www.ironvale.com</p>
      <svg class="divider-arrow" viewBox="0 0 10 20" aria-hidden="true">
        <path d="M5 1 L9 8 L6 8 L6 19 L4 19 L4 8 L1 8 Z" fill="var(--brand-red)"/>
      </svg>
      <p class="services">
        Forging <span class="dot">&bull;</span> Ports <span class="dot">&bull;</span> Fabrication <span class="dot">&bull;</span> Drilling<br>
        Power <span class="dot">&bull;</span> Northgate <span class="dot">&bull;</span> Eastbrook <span class="dot">&bull;</span> Port Alden<br>
        Stonebridge <span class="dot">&bull;</span> Westhaven
      </p>
    </section>
    <section class="card card-back" aria-label="Card back">
      <p class="brand-name">IRONVALE</p>
    </section>
  </main>
</body>
</html>
```